New Coffee Shop business card

We are opening our new coffee shop and are needing business cards to take with us on February 6th to Atlanta, Ga to a show.

We will be offering the following menu type items:

coffee
teas
espresso
frappes
smoothies

sandwiches
soups
salads
pastries
ice cream

Our shop is in a rural country-side area and we would like to convey that feel in our shop. In addition to the cafe we will also be selling gifts and furniture and other home decor. Much of this merchandise will be rescued, refurbished or repurposed which is also a core value of what we are all about.

We have a company logo we would like incorporated into the design.

We will also provide files that have the elements of the logo which may also be useful in the design of the card.

Since we are not open yet we need one slightly altered version of the card as well as the final product which states "Opening in the summer 2015"

Target Market(s)

moderate to slightly upscale and folksy.

Industry/Entity Type

Coffee Shop

Contact Information for Business Card

Fern Kettle Coffee
name
address
phone number
email

Card

Font styles to use
Sans Serif

Requirements
Must have
• Must include Logo
• Must include information on menu.
• Must include information on our merchandise sales as described inthe project description.
• Color scheme to complement the logo
Nice to have
• The following descriptions
• "We are also selling gifts, furniture, and other home decoration."
• "We rescue, refurbish, and repurpose old furniture so it can live again."

```html
<!DOCTYPE html>
<html lang="en">
<head>
<meta charset="utf-8">
<title>Fern Kettle Coffee – Business Cards</title>
<link rel="stylesheet" href="https://fonts.googleapis.com/css2?family=Jost:wght@400;500&family=Arimo:wght@400;700&display=swap">
<style>
  :root {
    --backdrop: #d6d6d4;
    --card: #0b0a0a;
    --white: #f3f1ee;
    --red: #93292d;
    --grey: #8c8c8c;
    --cream: #d8ccb4;
    --ember: #2a0d0d;
    --frame: #6e1f22;
  }
  * { box-sizing: border-box; margin: 0; padding: 0; }
  html, body { width: 1200px; height: 900px; overflow: hidden; }
  body {
    position: relative;
    background: var(--backdrop);
    font-family: "Jost", sans-serif;
    color: var(--white);
  }
  .card {
    position: absolute;
    background: var(--card);
    overflow: hidden;
    box-shadow: 0 2px 8px rgba(0,0,0,.35);
  }
  .card--front { left: 320px; top: 84px; width: 564px; height: 311px; }
  .card--back { left: 26px; top: 483px; width: 532px; height: 312px; }
  .card--opening { left: 620px; top: 438px; width: 560px; height: 312px; }

  /* word border */
  .word-band { position: absolute; font-size: 15px; white-space: nowrap; color: var(--grey); letter-spacing: .2px; }
  .word-band .coffee { color: var(--red); }
  .word-band .decor { color: var(--white); }
  .word-band .dot { color: var(--grey); margin: 0 7px; font-size: 11px; position: relative; top: -2px; }
  .word-band--top { top: 8px; left: 14px; }
  .word-band--left { writing-mode: vertical-rl; transform: rotate(180deg); left: 6px; bottom: 38px; }
  .word-band--right { writing-mode: vertical-rl; right: 6px; top: 38px; }

  .tagline {
    position: absolute; left: 0; right: 0; bottom: 12px;
    text-align: center; font-size: 15px; font-weight: 500; letter-spacing: .3px; color: var(--white);
  }
  .tagline .dot { color: var(--grey); font-size: 11px; margin: 0 8px; position: relative; top: -2px; }

  /* front */
  .brand {
    position: absolute; left: 60px; top: 52px; width: 210px; height: 210px;
    display: flex; flex-direction: column; align-items: center; justify-content: flex-end;
  }
  .brand__mark { width: 46px; height: 46px; border-radius: 50%; background: var(--white); margin-bottom: 22px; }
  .brand__name { font-size: 31px; font-weight: 400; color: var(--white); line-height: 1.1; text-align: center; }
  .pitch {
    position: absolute; left: 290px; top: 48px; width: 210px;
    text-align: center; font-size: 17px; line-height: 20px;
  }
  .pitch p { margin: 0; }
  .pitch__divider { display: block; width: 44px; height: 10px; margin: 6px auto 8px; background: var(--white); border-radius: 5px; opacity: .9; }
  .owners { margin-top: 14px !important; font-size: 11px; line-height: 14px; color: var(--cream); }

  /* back */
  .contact { position: absolute; text-align: center; }
  .card--back .contact { left: 60px; width: 250px; top: 46px; }
  .card--opening .contact { left: 40px; width: 280px; top: 48px; }
  .contact__phone { font-size: 23px; letter-spacing: 1px; line-height: 28px; color: var(--white); }
  .contact__line { font-family: "Arimo", sans-serif; font-size: 15px; line-height: 19px; color: var(--red); }

  .menu {
    position: absolute; width: 150px; height: 118px;
    border: 2px solid var(--frame); border-radius: 26px;
    outline: 1px solid #4a4a4a; outline-offset: 3px;
    text-align: center; font-family: "Arimo", sans-serif; font-size: 12px; line-height: 15px; color: var(--cream);
    padding-top: 22px;
  }
  .card--back .menu { left: 98px; top: 142px; }
  .card--opening .menu { left: 102px; top: 148px; height: 108px; padding-top: 18px; }
  .menu__title { color: var(--red); font-weight: 700; margin-bottom: 2px; }
  .menu__row { white-space: nowrap; margin: 0 -40px; }

  .steam-cup { position: absolute; background: linear-gradient(180deg, rgba(60,16,16,.55), rgba(42,13,13,.95)); border-radius: 60px 60px 20px 20px; }
  .card--back .steam-cup { left: 356px; top: 10px; width: 140px; height: 302px; opacity: .55; }
  .card--opening .steam-cup { left: 336px; top: 0; width: 180px; height: 312px; opacity: .55; }

  .opening {
    position: absolute; left: 354px; top: 46px;
    font-size: 31px; line-height: 32px; letter-spacing: 1px; font-weight: 400; color: var(--white);
  }
</style>
</head>
<body>

<!-- Front -->
<section class="card card--front">
  <div class="word-band word-band--top"><span class="dot">●</span><span class="coffee">coffee</span><span class="dot">●</span>gifts<span class="dot">●</span>furniture<span class="dot">●</span><span class="decor">home decor</span><span class="dot">●</span><span class="coffee">coffee</span><span class="dot">●</span>gifts<span class="dot">●</span>furniture<span class="dot">●</span></div>
  <div class="word-band word-band--left"><span class="decor">home decor</span><span class="dot">●</span><span class="coffee">coffee</span><span class="dot">●</span>gifts</div>
  <div class="word-band word-band--right"><span class="decor">home decor</span><span class="dot">●</span><span class="coffee">coffee</span><span class="dot">●</span>gifts</div>

  <div class="brand">
    <span class="brand__mark"></span>
    <span class="brand__name">Fern Kettle<br>Coffee</span>
  </div>

  <div class="pitch">
    <p>Not just a coffee shop</p>
    <span class="pitch__divider" role="img" aria-label="Small flourish divider"></span>
    <p>Come visit, eat,<br>or peruse the "stuff<br>we're selling"</p>
    <span class="pitch__divider" role="img" aria-label="Small flourish divider"></span>
    <p>an eclectic assemblage<br>of furnishings,<br>gifts, and home decor.</p>
    <p class="owners">Owners: Dale and Mara Quinlan</p>
  </div>

  <p class="tagline">We rescue, refurbish and repurpose old furniture so it can live again</p>
</section>

<!-- Back -->
<section class="card card--back">
  <div class="steam-cup" role="img" aria-label="Faint steaming coffee cup decoration"></div>
  <div class="word-band word-band--top"><span class="dot">●</span><span class="coffee">coffee</span><span class="dot">●</span>gifts<span class="dot">●</span>furniture<span class="dot">●</span><span class="decor">home decor</span><span class="dot">●</span><span class="coffee">coffee</span><span class="dot">●</span>gifts<span class="dot">●</span>furniture<span class="dot">●</span></div>
  <div class="word-band word-band--left"><span class="decor">home decor</span><span class="dot">●</span><span class="coffee">coffee</span><span class="dot">●</span>gifts</div>
  <div class="word-band word-band--right"><span class="decor">home decor</span><span class="dot">●</span><span class="coffee">coffee</span><span class="dot">●</span>gifts</div>

  <div class="contact">
    <p class="contact__phone">1404 5 820 913</p>
    <p class="contact__line">18 Millbrook Rd Ste 4,</p>
    <p class="contact__line">Atlanta GA 30310</p>
    <p class="contact__line">hello@fernkettle.com</p>
  </div>

  <div class="menu">
    <p class="menu__title">MENU:</p>
    <p class="menu__row">coffee&nbsp; teas&nbsp; espresso</p>
    <p class="menu__row">frappes smoothies sandwiches</p>
    <p class="menu__row">soups&nbsp;&nbsp; salads&nbsp; pastries</p>
    <p class="menu__row">ice cream</p>
  </div>

  <p class="tagline">We rescue, refurbish and repurpose old furniture so it can live again <span class="dot">●</span></p>
</section>

<!-- Pre-opening back -->
<section class="card card--opening">
  <div class="steam-cup" role="img" aria-label="Faint steaming coffee cup decoration"></div>
  <div class="word-band word-band--top"><span class="dot">●</span><span class="coffee">coffee</span><span class="dot">●</span>gifts<span class="dot">●</span>furniture<span class="dot">●</span><span class="decor">home decor</span><span class="dot">●</span><span class="coffee">coffee</span><span class="dot">●</span>gifts<span class="dot">●</span>furniture<span class="dot">●</span></div>
  <div class="word-band word-band--left"><span class="decor">home decor</span><span class="dot">●</span><span class="coffee">coffee</span><span class="dot">●</span>gifts</div>
  <div class="word-band word-band--right"><span class="decor">home decor</span><span class="dot">●</span><span class="coffee">coffee</span><span class="dot">●</span>gifts</div>

  <div class="contact">
    <p class="contact__phone">1404 5 820 913</p>
    <p class="contact__line">18 Millbrook Rd Ste 4,</p>
    <p class="contact__line">Atlanta GA 30310</p>
    <p class="contact__line">hello@fernkettle.com</p>
  </div>

  <div class="menu">
    <p class="menu__title">MENU:</p>
    <p class="menu__row">coffee&nbsp; teas&nbsp; espresso</p>
    <p class="menu__row">frappes smoothies sandwiches</p>
    <p class="menu__row">soups&nbsp;&nbsp; salads&nbsp; pastries</p>
    <p class="menu__row">ice cream</p>
  </div>

  <h2 class="opening">OPENING<br>IN THE<br>SUMMER<br>2015</h2>

  <p class="tagline">We rescue, refurbish and repurpose old furniture so it can live again <span class="dot">●</span></p>
</section>

</body>
</html>
```